Pediatric Practice Flyer Design

I need marketing flyer created for distribution. It is for a pediatric clinic. Need some realistic eye catching design and content. I already have a logo that will go on top of the flyer. I will be using lumoraxen for flyer print service. So need it copyable for printing. Again, need eye catching content as well. We are planning on opening the clinic in December.

```html
<!DOCTYPE html>
<html lang="en">
<head>
<meta charset="utf-8">
<title>Maple Sprout Care Pediatrics – Opening Flyer</title>
<link rel="stylesheet" href="https://fonts.googleapis.com/css2?family=Baloo+2:wght@700;800&family=Oswald:wght@500;600&family=Roboto:wght@400;500;700&family=Lora:ital,wght@0,600;1,600&display=swap">
<style>
  :root {
    --surround: #dcdcdc;
    --paper: #ffffff;
    --ink: #1d1d1f;
    --brand-blue: #1f6fb5;
    --band-blue: #1e78c8;
    --band-purple: #6a2d91;
    --orange: #f39a2b;
    --pink: #e0177f;
    --teal: #1ba39c;
    --red: #e32128;
    --purple: #6b2c8f;
    --photo-warm: #e9dcd2;
    --photo-cool: #cfe0e6;
  }
  * { box-sizing: border-box; margin: 0; padding: 0; }
  html, body { width: 1200px; height: 1177px; overflow: hidden; }
  body { background: var(--surround); position: relative; font-family: "Roboto", Arial, sans-serif; color: var(--ink); }

  .flyer {
    position: absolute; left: 232px; top: 120px;
    width: 746px; height: 966px;
    background: var(--paper);
    box-shadow: 0 2px 8px rgba(0,0,0,.18);
    overflow: hidden;
  }
  .shapes { position: absolute; inset: 0; width: 746px; height: 966px; }

  .brand { position: absolute; left: 46px; top: 44px; display: flex; align-items: center; gap: 18px; }
  .brand-dot { width: 86px; height: 86px; border-radius: 50%; background: var(--orange); }
  .brand-name { font-family: "Baloo 2", sans-serif; font-weight: 800; color: var(--red); font-size: 46px; line-height: 1; }
  .brand-name span { display: block; font-size: 26px; margin-top: 6px; }

  .doctor { position: absolute; left: 42px; top: 184px; font-family: "Baloo 2", sans-serif; font-weight: 800; font-size: 40px; line-height: 48px; color: var(--brand-blue); }

  .services { position: absolute; left: 134px; top: 232px; list-style: none; font-size: 15.5px; line-height: 20.4px; }
  .services li::before { content: "• "; }
  .services .wrap { padding-left: 12px; }
  .services .wrap::before { content: ""; }

  .photo { position: absolute; }
  .photo-exam { left: 18px; top: 454px; width: 410px; height: 238px; background: linear-gradient(120deg, var(--photo-warm), #f6eee8 55%, #dfe6ee); }
  .photo-boy { left: 464px; top: 622px; width: 282px; height: 320px; background: linear-gradient(160deg, #f4f1ec, var(--photo-cool) 70%, #b9cfd8); }

  .opening { position: absolute; left: 362px; top: 470px; width: 290px; text-align: center; color: #fff; }
  .opening-title { font-family: "Oswald", sans-serif; font-weight: 600; font-size: 56px; line-height: 54px; letter-spacing: 1px; }
  .opening-rule { width: 172px; margin: 10px auto 6px; border-top: 2px dotted #fff; }
  .opening-date { font-family: "Lora", serif; font-weight: 600; font-size: 32px; line-height: 40px; }

  .offer-main { position: absolute; left: 40px; top: 712px; line-height: 40px; white-space: nowrap; border-bottom: 3px solid var(--purple); }
  .offer-free { font-family: "Oswald", sans-serif; font-weight: 600; font-size: 38px; color: var(--red); }
  .offer-text { font-family: "Roboto", sans-serif; font-weight: 700; font-size: 27px; color: var(--purple); }
  .offer-sub { position: absolute; left: 40px; top: 758px; line-height: 30px; font-family: "Lora", serif; font-style: italic; font-weight: 600; font-size: 24px; color: var(--teal); white-space: nowrap; }
  .offer-call { position: absolute; left: 127px; top: 796px; line-height: 18px; font-weight: 500; font-size: 15px; color: var(--pink); white-space: nowrap; }

  .contact { position: absolute; left: 0; top: 822px; width: 520px; height: 120px; color: #fff; font-size: 16.5px; font-style: normal; }
  .contact-line { position: absolute; line-height: 22px; white-space: nowrap; }
  .contact-web { font-weight: 700; font-size: 20px; line-height: 24px; }
  .icon { position: absolute; width: 16px; height: 16px; }
</style>
</head>
<body>
<main class="flyer">
  <svg class="shapes" viewBox="0 0 746 966" aria-hidden="true">
    <polygon points="650,0 746,0 746,168" fill="var(--teal)"/>
    <polygon points="606,256 734,256 668,366" fill="var(--orange)"/>
    <polygon points="668,370 580,444 752,444" fill="var(--pink)"/>
  </svg>

  <header class="brand">
    <div class="brand-dot"></div>
    <div class="brand-name">Maple Sprout<span>Care Pediatrics</span></div>
  </header>

  <h1 class="doctor">Dr. Elena Marsh</h1>

  <ul class="services">
    <li>Award winning experienced doctor</li>
    <li>Personalized and comprehensive child healthcare from</li>
    <li class="wrap">birth - 21 years of age ranging from but not limited to:</li>
    <li>Well Child Care - Annual Physicals</li>
    <li>Immunization - Sports/Camp Physicals</li>
    <li>Behavioral and Development Screening</li>
    <li>SAME DAY APPOINTMENTS FOR SICK/WELL CHILD VISIT</li>
    <li>Direct Accessibility to the Doctor</li>
    <li>Conveniently located near Riverbend Medical</li>
    <li>CONVENIENT HOURS: MONDAY - SATURDAY</li>
  </ul>

  <div class="photo photo-exam" role="img" aria-label="Photo of a smiling doctor listening to a young girl's heartbeat with a stethoscope"></div>
  <div class="photo photo-boy" role="img" aria-label="Photo of a toddler boy being checked with a stethoscope during a visit"></div>

  <svg class="shapes" viewBox="0 0 746 966" aria-hidden="true">
    <polygon points="306,454 712,454 504,804" fill="var(--orange)"/>
    <polygon points="56,822 106,822 40,942 0,942 0,918" fill="var(--band-purple)"/>
    <polygon points="106,822 498,822 468,942 40,942" fill="var(--band-blue)"/>
    <rect x="0" y="942" width="746" height="24" fill="var(--pink)"/>
  </svg>

  <div class="opening">
    <div class="opening-title">OPENING<br>SOON</div>
    <div class="opening-rule"></div>
    <div class="opening-date">December<br>2022</div>
  </div>

  <section class="offer">
    <div class="offer-main"><span class="offer-free">FREE</span> <span class="offer-text">1st Consultation</span></div>
    <div class="offer-sub">Accepting New Patients</div>
    <div class="offer-call">PLEASE CALL FOR DETAILS</div>
  </section>

  <address class="contact">
    <svg class="icon" style="left:66px;top:14px" viewBox="0 0 16 16"><path d="M8 1a5 5 0 0 0-5 5c0 4 5 9 5 9s5-5 5-9a5 5 0 0 0-5-5zm0 7a2 2 0 1 1 0-4 2 2 0 0 1 0 4z" fill="#fff"/></svg>
    <span class="contact-line" style="left:109px;top:13px">482 Birchwood Ave, Suite 12, Hollis NC 27999.</span>
    <svg class="icon" style="left:52px;top:37px" viewBox="0 0 16 16"><path d="M3 1l3 3-1.5 2a9 9 0 0 0 5.5 5.5L12 10l3 3-2 2C7 15 1 9 1 3z" fill="#fff"/></svg>
    <span class="contact-line" style="left:97px;top:37px">555-301-4172</span>
    <svg class="icon" style="left:224px;top:40px" viewBox="0 0 16 16"><path d="M4 1h8v4H4zM1 6h14v6h-3v3H4v-3H1zm4 4v3h6v-3z" fill="#fff"/></svg>
    <span class="contact-line" style="left:252px;top:37px">555-301-4190</span>
    <svg class="icon" style="left:42px;top:58px" viewBox="0 0 16 16"><path d="M1 3h14v10H1zm1.5 1.5V5L8 9l5.5-4v-.5zm0 2.3v4.7h11V6.8L8 10.8z" fill="#fff"/></svg>
    <span class="contact-line" style="left:78px;top:59px">office@maplesproutpeds.com</span>
    <svg class="icon" style="left:26px;top:89px" viewBox="0 0 16 16"><circle cx="8" cy="8" r="6.5" fill="none" stroke="#fff" stroke-width="1.5"/><path d="M1.5 8h13M8 1.5c-3 3.5-3 9.5 0 13M8 1.5c3 3.5 3 9.5 0 13" fill="none" stroke="#fff" stroke-width="1.2"/></svg>
    <span class="contact-line contact-web" style="left:55px;top:85px">www.maplesproutpeds.com</span>
  </address>
</main>
</body>
</html>
```